Card Design Project

A simple, funky, cool birth announcement card
Not corporate, but arty
Not childish nor girlish
No baby pictures

Text is tbc (eg name and date may change)

Front side: just the name "fenna"
Should be easy to read

Back side text (in Dutch):

We vinden je nu al leuk!

20 JUNE 2013
Singapore

Dochter van Marieke Dorrel & Joost Vermalen

Yangon, Myanmar
+95 1 64 8319
Callio: Marieke.Dorrel
Callio: Joost.Vermalen

Size will be A6
Updates

Reason: Dear designers, At this stage we would like to have one or more designers to draft up the card (of which the final text is still tbd as the baby is yet to be born) using the typeface used on the left below (or similar!) of the newly added picture - in black - in fluorescent colours Can you get back to us in a few days? Thanks

Target Market(s)

Our funky friends in holland.

Industry/Entity Type

Baby

Requirements
Must have
• Colours, aswe are very happy to welcome this baby.
Something that makes it stand out from all other baby birth announcement cards

A6 size
Deadline 21 June
Printing will be on white (thick paper 250g)
Design for 5mm "bleedsides" all around
At least available in PDF (and other formats)
Nice to have
• We've recently moved from netherlands to Yangon
We could include the iconic kyauktaran pagoda

I would like for it to look like a cool party announcement

Include bright fluoriscent colours, including orange.
The enveloppe will be orange
Should not have
• Any baby stuff, soft pink dominance, childish stuff.

```html
<!DOCTYPE html>
<html lang="nl">
<head>
<meta charset="utf-8">
<title>Geboortekaart – achterkant</title>
<link href="https://fonts.googleapis.com/css2?family=Barlow:wght@400;500;600;700&family=Caveat+Brush&display=swap" rel="stylesheet">
<style>
  :root {
    --hot-pink: #ff0d5f;
    --lime: #d2f000;
    --magenta: #d424d8;
    --ink: #333333;
    --grey-top: #e6e6e6;
    --grey-bottom: #fbfbfb;
    --divider-green: #8fd12a;
  }
  * { margin: 0; padding: 0; box-sizing: border-box; }
  html, body { width: 1200px; height: 799px; overflow: hidden; background: #ffffff; }
  .card {
    position: relative;
    width: 1200px;
    height: 799px;
    overflow: hidden;
    background: #ffffff;
    font-family: "Barlow", Arial, sans-serif;
  }
  .headline {
    position: absolute;
    left: 0;
    top: 30px;
    width: 1200px;
    text-align: center;
    font-family: "Caveat Brush", cursive;
    font-weight: 400;
    font-size: 188px;
    line-height: 206px;
    color: var(--hot-pink);
  }
  .headline span { display: block; }
  .headline .line-two { padding-right: 70px; }
  .spectrum {
    position: absolute;
    left: 0;
    top: 503px;
    width: 1200px;
    height: 7px;
    background: linear-gradient(90deg, #d822d0 0%, #ff1c6a 28%, #ff3a3a 42%, #f28a10 55%, #c8ff00 72%, #8cf06a 85%, #3ee0f0 100%);
  }
  .details {
    position: absolute;
    left: 0;
    top: 510px;
    width: 1200px;
    height: 289px;
    background: linear-gradient(180deg, var(--grey-top) 0%, var(--grey-bottom) 100%);
  }
  .birth {
    position: absolute;
    left: 182px;
    top: 104px;
    width: 360px;
    text-align: center;
  }
  .birth-date {
    font-size: 58px;
    font-weight: 700;
    color: var(--lime);
    line-height: 1;
  }
  .birth-place {
    margin-top: 4px;
    font-size: 23px;
    font-weight: 500;
    color: var(--ink);
  }
  .parents {
    position: absolute;
    left: 677px;
    top: 40px;
    color: var(--ink);
  }
  .parents-names {
    font-size: 27px;
    font-weight: 700;
    line-height: 34px;
  }
  .parents-contact {
    margin-top: 18px;
    font-size: 22px;
    font-weight: 500;
  }
  .parents-contact .sep { color: var(--divider-green); margin: 0 6px; }
  .chat-list { margin-top: 22px; list-style: none; }
  .chat-list li { font-size: 23px; font-weight: 500; line-height: 33px; }
  .chat-label {
    font-size: 15px;
    font-weight: 500;
    color: var(--magenta);
    margin-right: 6px;
    text-transform: uppercase;
  }
</style>
</head>
<body>
<div class="card">
  <h1 class="headline"><span>We vinden je</span><span class="line-two">nu al leuk!</span></h1>
  <div class="spectrum"></div>
  <section class="details">
    <div class="birth">
      <p class="birth-date">20 JUNE 2013</p>
      <p class="birth-place">Singapore</p>
    </div>
    <div class="parents">
      <p class="parents-names">Dochter van Marieke Dorrel<br>&amp; Joost Vermalen</p>
      <p class="parents-contact">Yangon, Myanmar<span class="sep">|</span>+95 1 64 8319</p>
      <ul class="chat-list">
        <li><span class="chat-label">Callio:</span>Marieke.Dorrel</li>
        <li><span class="chat-label">Callio:</span>Joost.Vermalen</li>
      </ul>
    </div>
  </section>
</div>
</body>
</html>
```